High-Converting Facebook Ads for Portals Drapes & Louvres (6 Products)

We are looking for a graphic designer to create high-quality Facebook & Instagram ads for our business: Portals Drapes and Louvres (Melbourne, Australia).

We require 6 separate ad designs, each for a different product:

Zipscreen Blinds

Outdoor Awnings

Plantation Shutters

Roller Shutters

Security Doors

Roller Blinds & Sheer Curtains

Ad Specifications:

Sizes:

1440 x 1800 px (4:5 ratio)

1080 x 1080 px (1:1 ratio)

1080 x 1920 px (9:16 ratio for Stories/Reels)

Format: PNG (high resolution, not blurry)

Designed specifically for Meta (Facebook/Instagram ads)

Mobile-friendly layout (clear, easy to read)

Style:

Bold, sales-driven, retail-style ads (NOT minimal)

Eye-catching and designed to generate leads

Clean, professional layout

Similar to promotional home improvement ads

Brand Colours:

Red: #E31E24

Blue: #0072BC

White backgrounds

Each ad must include:

“SALE NOW ON” banner at top

Our showroom address:
482 Upper Wattleby Road, Kestrel Heights (must be fully visible, not cut off)

Phone number: 9471 2658

Our logo (provided)

Badge: “Celebrating 13 YEARS in Business” (must be clean and readable)

Call to Action:

For 5 ads: “Book a FREE quote TODAY!”

For Security Doors ad: “ORDER NOW”

Offers / Pricing:

Most products: “UP TO 40% OFF”

Plantation Shutters: “FROM $299/sqm”

Security Doors: “FROM $750”

Content for each ad (examples):

Zipscreen Blinds:

Made to Measure

Fully Installed

Wind, Sun & Insect Protection

Outdoor Awnings:

Reduce Heat & Glare

Energy Saving

Custom Made

Plantation Shutters:

Modern & Elegant

Light & Privacy Control

Durable & Easy Care

Roller Shutters:

Security Protection

Block Heat & Noise

Total Light Control

Security Doors:

3 Point Locking

Premium Mesh

Custom Made

Blinds & Sheers:

Huge Range of Fabrics

Modern Soft Finish

Perfect for Any Room

Important Notes:

All text must be sharp and easy to read (no blur)

Layout must be balanced and not overcrowded

Ensure no text is cut off (especially address and headings)

Badge text must be straight and professional (no distortion)

Use high-quality, relevant images (we will provide references)

Goal:
Create ads that look professional, trustworthy, and generate enquiries/bookings for in-home quotes.

We are open to creative ideas but want a strong, bold retail-style ad that converts.
I have uploaed chatgpt mocks

Target Market(s)

Homeowners in Melbourne, Australia (typically aged 30–65) looking to improve their homes with blinds, shutters, awnings and security doors. Mid to high income households focused on quality, security, and modern home upgrades.

Industry/Entity Type

Home Improvement / Construction / Retail

Font styles to use
Sans Serif

Requirements
Must have
• Clear, bold and easy-to-read text (must be readable on mobile) High-quality, non-blurry design Strong “SALE” style layout (retail promotional look) Proper spacing (no overcrowded designs) All key info visible (address must NOT be cut off) Correct pricing and offers included Clean “13 YEARS” badge (no distortion or curved text) Consistent branding across all 6 ads
Nice to have
• Modern, slightly premium feel while still being bold Good use of contrast (red/blue/white) Subtle shadows or layering to improve depth Clean use of icons or bullet points Strong hierarchy (headline → benefits → offer → CTA) Variations in layout for testing different ad styles
Should not have
• Minimal or plain designs (we want bold, sales-driven ads) Hard-to-read fonts or script fonts Low-quality or blurry images Overcrowded layouts with too much text Important text cut off (especially address or headings) Overuse of effects or “cheap” looking graphics Yellow-heavy colour schemes (must follow brand colours)

```html
<!DOCTYPE html>
<html lang="en">
<head>
<meta charset="utf-8">
<title>Portals Drapes &amp; Louvres – Sale Ad Set</title>
<link rel="stylesheet" href="https://fonts.googleapis.com/css2?family=Oswald:wght@600;700&family=Montserrat:wght@700;800;900&display=swap">
<style>
  :root{
    --board:#58666d;
    --blue:#1b5f9b;
    --blue-deep:#134a7c;
    --red:#d5121b;
    --red-deep:#a80c12;
    --yellow:#f6c700;
    --ink:#151515;
    --white:#ffffff;
    --gold-1:#fff1a8;
    --gold-2:#e7a81c;
    --gold-3:#a8680a;
  }
  *{box-sizing:border-box;margin:0;padding:0}
  html,body{width:1200px;height:898px;overflow:hidden;background:var(--board)}
  .board{position:relative;width:1200px;height:898px;background:var(--board)}

  .ad{position:absolute;width:364px;height:364px;overflow:hidden;background:var(--blue)}
  .ad--doors{left:39px;top:71px}
  .ad--shutters{left:419px;top:71px}
  .ad--awnings{left:800px;top:71px}
  .ad--sheers{left:39px;top:448px}
  .ad--zip{left:419px;top:448px}

  .photo{position:absolute}
  .panel{position:absolute}
  .panel--white{background:var(--white)}
  .panel--blue{background:linear-gradient(180deg,var(--blue) 0%,var(--blue-deep) 100%)}

  /* brand block */
  .brand{position:absolute;display:flex;flex-direction:column;align-items:center;justify-content:center;gap:4px;background:var(--white)}
  .brand-mark{width:18px;height:18px;background:var(--red)}
  .brand-name{font-family:"Montserrat",sans-serif;font-weight:800;font-size:12px;line-height:1.1;color:var(--blue);text-align:center}

  /* sale banner */
  .sale-banner{position:absolute;height:90px;transform:rotate(-5deg);transform-origin:0 100%}
  .offer-tag{position:absolute;left:12px;top:0;height:19px;padding:0 14px 0 6px;background:var(--yellow);
    font-family:"Oswald",sans-serif;font-weight:700;font-size:14px;line-height:19px;color:var(--ink);
    clip-path:polygon(0 0,88% 0,100% 50%,88% 100%,0 100%);white-space:nowrap}
  .sale-band{position:absolute;left:0;right:0;top:17px;height:54px;
    background:linear-gradient(180deg,#3a3a3a 0%,var(--ink) 55%,#050505 100%);
    border-bottom:2px solid var(--red);border-top:2px solid var(--red);
    display:flex;align-items:center;padding-left:8px;box-shadow:0 3px 6px rgba(0,0,0,.35)}
  .sale-title{font-family:"Oswald",sans-serif;font-weight:700;font-size:var(--fs,36px);letter-spacing:-1px;
    color:#f2f2f2;white-space:nowrap;line-height:1}
  .buy-tag{position:absolute;right:6px;top:58px;height:21px;padding:0 8px;background:var(--red);
    font-family:"Oswald",sans-serif;font-weight:700;font-size:15px;line-height:21px;color:var(--yellow);white-space:nowrap}

  /* features */
  .feature-list{position:absolute;list-style:none;display:flex;flex-direction:column}
  .feature{display:flex;align-items:flex-start;gap:8px}
  .feature-icon{flex:0 0 18px;width:18px;height:18px;margin-top:3px}
  .feature-text{font-family:"Oswald",sans-serif;font-weight:700;font-size:var(--ff,21px);line-height:1.08;color:var(--white);white-space:nowrap}

  /* badge */
  .badge{position:absolute;width:80px;height:96px}
  .badge-ribbon{position:absolute;top:58px;width:18px;height:34px;background:var(--blue-deep);clip-path:polygon(0 0,100% 0,100% 100%,50% 78%,0 100%)}
  .badge-ribbon--left{left:20px;transform:rotate(22deg)}
  .badge-ribbon--right{right:20px;transform:rotate(-22deg)}
  .badge-seal{position:absolute;left:0;top:0;width:80px;height:80px;border-radius:50%;
    background:radial-gradient(circle at 35% 30%,var(--gold-1) 0%,var(--gold-2) 45%,var(--gold-3) 100%);
    box-shadow:0 2px 5px rgba(0,0,0,.35);display:flex;align-items:center;justify-content:center}
  .badge-core{width:58px;height:58px;border-radius:50%;background:radial-gradient(circle at 40% 35%,#2f7fd0 0%,#123f7a 100%);
    border:2px solid #ffe58a;display:flex;flex-direction:column;align-items:center;justify-content:center;
    font-family:"Oswald",sans-serif;color:var(--white);text-align:center;line-height:1}
  .badge-small{font-size:7px;font-weight:600}
  .badge-big{font-size:13px;font-weight:700;margin:1px 0}
  .badge-tiny{font-size:6px;font-weight:600}

  /* call to action */
  .cta{position:absolute;font-family:"Montserrat",sans-serif;font-weight:900;font-size:15px;line-height:1.05;color:var(--ink);white-space:nowrap}
  .order-now{font-size:19px;text-align:center}

  /* footer */
  .contact-bar{position:absolute;left:0;bottom:0;width:364px;height:23px;background:linear-gradient(90deg,var(--red-deep),var(--red) 50%,var(--red-deep));
    display:flex;align-items:center;justify-content:space-between;padding:0 12px 0 10px;
    font-family:"Montserrat",sans-serif;font-weight:800;color:var(--white);white-space:nowrap}
  .contact-address{font-size:9.4px}
  .contact-phone{display:flex;align-items:center;gap:5px;font-size:13px}
  .contact-phone svg{width:13px;height:13px}
</style>
</head>
<body>
<main class="board">

  <!-- Security Doors -->
  <section class="ad ad--doors">
    <div class="photo" style="left:213px;top:0;width:151px;height:341px;background:linear-gradient(90deg,#8b7b6c 0%,#4a3a33 30%,#3b2c27 70%,#7d6b5b 100%)" role="img" aria-label="Dark timber security door set in a brick entry"></div>
    <div class="brand" style="left:0;top:0;width:148px;height:78px">
      <span class="brand-mark"></span>
      <span class="brand-name">Portals Drapes<br>&amp; Louvres</span>
    </div>
    <div class="sale-banner" style="left:0;top:82px;width:205px;--fs:35px">
      <span class="offer-tag">FROM $750</span>
      <div class="sale-band"><span class="sale-title">SALE NOW ON</span></div>
      <span class="buy-tag">BUY NOW</span>
    </div>
    <ul class="feature-list" style="left:16px;top:181px;gap:9px">
      <li class="feature"><svg class="feature-icon" viewBox="0 0 18 18" fill="none" stroke="#fff" stroke-width="1.6"><rect x="4" y="1.5" width="8" height="15" rx="1"/><path d="M6 5h4M6 8h4"/></svg><span class="feature-text">3 Point Locking</span></li>
      <li class="feature"><svg class="feature-icon" viewBox="0 0 18 18" fill="none" stroke="#fff" stroke-width="1.4"><rect x="2" y="2" width="14" height="14"/><path d="M2 6.7h14M2 11.3h14M6.7 2v14M11.3 2v14"/></svg><span class="feature-text">Premium Mesh</span></li>
      <li class="feature"><svg class="feature-icon" viewBox="0 0 18 18" fill="none" stroke="#fff" stroke-width="1.6"><rect x="7" y="1.5" width="9" height="15"/><circle cx="4" cy="13" r="2.5"/></svg><span class="feature-text">Custom Made</span></li>
    </ul>
    <div class="panel panel--white" style="left:0;top:288px;width:213px;height:53px"></div>
    <div class="photo" style="left:12px;top:294px;width:34px;height:42px;background:linear-gradient(180deg,#2b2b2b,#111)" role="img" aria-label="Digital door handle set"></div>
    <span class="cta order-now" style="left:52px;top:296px">ORDER<br>NOW</span>
    <div class="photo" style="left:174px;top:290px;width:28px;height:51px;background:linear-gradient(180deg,#3d312c,#241b18)" role="img" aria-label="Small security door product shot"></div>
    <div class="badge" style="left:176px;top:236px">
      <span class="badge-ribbon badge-ribbon--left"></span><span class="badge-ribbon badge-ribbon--right"></span>
      <div class="badge-seal"><div class="badge-core"><span class="badge-small">Celebrating</span><span class="badge-big">13 YEARS</span><span class="badge-tiny">in Business</span></div></div>
    </div>
    <footer class="contact-bar">
      <span class="contact-address">482 Upper Wattleby Road, Kestrel Heights</span>
      <span class="contact-phone"><svg viewBox="0 0 24 24" fill="#fff"><path d="M6.6 10.8a15 15 0 0 0 6.6 6.6l2.2-2.2c.3-.3.7-.4 1-.2 1.1.4 2.3.6 3.6.6.6 0 1 .4 1 1V20c0 .6-.4 1-1 1A17 17 0 0 1 3 4c0-.6.4-1 1-1h3.5c.6 0 1 .4 1 1 0 1.3.2 2.5.6 3.6.1.3 0 .7-.2 1z"/></svg>9471 2658</span>
    </footer>
  </section>

  <!-- Roller Shutters -->
  <section class="ad ad--shutters">
    <div class="photo" style="left:0;top:0;width:225px;height:341px;background:linear-gradient(120deg,#dfe3e8 0%,#9fb3c6 35%,#b9a4b8 60%,#6f7f95 100%)" role="img" aria-label="Woman with a mug standing beside window roller shutters"></div>
    <div class="brand" style="left:225px;top:0;width:139px;height:84px">
      <span class="brand-mark"></span>
      <span class="brand-name">Portals Drapes<br>&amp; Louvres</span>
    </div>
    <div class="panel panel--blue" style="left:225px;top:84px;width:139px;height:212px"></div>
    <div class="sale-banner" style="left:0;top:8px;width:222px;--fs:40px">
      <span class="offer-tag">UP TO 40% OFF</span>
      <div class="sale-band"><span class="sale-title">SALE NOW ON</span></div>
      <span class="buy-tag">BUY NOW</span>
    </div>
    <ul class="feature-list" style="left:233px;top:116px;gap:10px;--ff:21px">
      <li class="feature"><svg class="feature-icon" viewBox="0 0 18 18" fill="none" stroke="#fff" stroke-width="1.6"><path d="M9 1.5 15 4v5c0 4-3 6.5-6 7.5C6 15.5 3 13 3 9V4z"/><path d="M6.5 9l2 2 3-3.5"/></svg><span class="feature-text">Security<br>Protection</span></li>
      <li class="feature"><svg class="feature-icon" viewBox="0 0 18 18" fill="none" stroke="#fff" stroke-width="1.6"><path d="M2 9 9 3l7 6M4 8v8h10V8"/><rect x="7" y="11" width="4" height="5"/></svg><span class="feature-text">Block Heat<br>&amp; Noise</span></li>
      <li class="feature"><svg class="feature-icon" viewBox="0 0 18 18" fill="none" stroke="#fff" stroke-width="1.6"><rect x="2" y="3" width="14" height="10"/><path d="M5 10a4 4 0 0 1 8 0M2 16h14"/></svg><span class="feature-text">Total Light<br>Control</span></li>
    </ul>
    <div class="panel panel--white" style="left:225px;top:296px;width:139px;height:45px"></div>
    <span class="cta" style="left:233px;top:302px;font-size:14.5px">Book a FREE<br>quote TODAY!</span>
    <div class="badge" style="left:33px;top:220px">
      <span class="badge-ribbon badge-ribbon--left"></span><span class="badge-ribbon badge-ribbon--right"></span>
      <div class="badge-seal"><div class="badge-core"><span class="badge-small">Celebrating</span><span class="badge-big">13 YEARS</span><span class="badge-tiny">in Business</span></div></div>
    </div>
    <footer class="contact-bar">
      <span class="contact-address">482 Upper Wattleby Road, Kestrel Heights</span>
      <span class="contact-phone"><svg viewBox="0 0 24 24" fill="#fff"><path d="M6.6 10.8a15 15 0 0 0 6.6 6.6l2.2-2.2c.3-.3.7-.4 1-.2 1.1.4 2.3.6 3.6.6.6 0 1 .4 1 1V20c0 .6-.4 1-1 1A17 17 0 0 1 3 4c0-.6.4-1 1-1h3.5c.6 0 1 .4 1 1 0 1.3.2 2.5.6 3.6.1.3 0 .7-.2 1z"/></svg>9471 2658</span>
    </footer>
  </section>

  <!-- Outdoor Awnings -->
  <section class="ad ad--awnings">
    <div class="panel panel--blue" style="left:0;top:0;width:224px;height:214px"></div>
    <div class="brand" style="left:224px;top:0;width:140px;height:70px">
      <span class="brand-mark"></span>
      <span class="brand-name">Portals Drapes<br>&amp; Louvres</span>
    </div>
    <div class="photo" style="left:224px;top:70px;width:140px;height:144px;background:linear-gradient(135deg,#f3f3f3 0%,#e6b9bd 40%,#c9414b 70%,#eee 100%)" role="img" aria-label="Red and white striped window awnings on a white wall"></div>
    <div class="photo" style="left:0;top:214px;width:224px;height:127px;background:linear-gradient(170deg,#c9b59b 0%,#c96a6f 35%,#3e5a3a 75%,#2b3a2a 100%)" role="img" aria-label="Striped folding-arm awning over a stone patio"></div>
    <div class="panel panel--white" style="left:224px;top:214px;width:140px;height:127px"></div>
    <div class="sale-banner" style="left:0;top:4px;width:178px;--fs:33px">
      <span class="offer-tag">UP TO 40% OFF</span>
      <div class="sale-band"><span class="sale-title">SALE NOW ON</span></div>
      <span class="buy-tag">BUY NOW</span>
    </div>
    <ul class="feature-list" style="left:10px;top:99px;gap:10px">
      <li class="feature"><svg class="feature-icon" viewBox="0 0 18 18" fill="none" stroke="#fff" stroke-width="1.6"><circle cx="8" cy="9" r="3"/><path d="M8 2v2M8 14v2M1 9h2M3 4l1.4 1.4M3 14l1.4-1.4M14 3v10"/></svg><span class="feature-text">Reduce Heat &amp; Glare</span></li>
      <li class="feature"><svg class="feature-icon" viewBox="0 0 18 18" fill="none" stroke="#fff" stroke-width="1.6"><rect x="5" y="3" width="8" height="13" rx="1"/><path d="M7.5 1.5h3M7 10h4M7 13h4"/></svg><span class="feature-text">Energy Saving</span></li>
      <li class="feature"><svg class="feature-icon" viewBox="0 0 18 18" fill="none" stroke="#fff" stroke-width="1.6"><path d="M4 2v14M9 2v14M14 2v14"/><path d="M2 6h4M7 11h4M12 7h4"/></svg><span class="feature-text">Custom Made</span></li>
    </ul>
    <div class="badge" style="left:254px;top:195px">
      <span class="badge-ribbon badge-ribbon--left"></span><span class="badge-ribbon badge-ribbon--right"></span>
      <div class="badge-seal"><div class="badge-core"><span class="badge-small">Celebrating</span><span class="badge-big">13 YEARS</span><span class="badge-tiny">in Business</span></div></div>
    </div>
    <span class="cta" style="left:236px;top:296px;font-size:14.5px">Book a FREE<br>quote TODAY!</span>
    <footer class="contact-bar">
      <span class="contact-address">482 Upper Wattleby Road, Kestrel Heights</span>
      <span class="contact-phone"><svg viewBox="0 0 24 24" fill="#fff"><path d="M6.6 10.8a15 15 0 0 0 6.6 6.6l2.2-2.2c.3-.3.7-.4 1-.2 1.1.4 2.3.6 3.6.6.6 0 1 .4 1 1V20c0 .6-.4 1-1 1A17 17 0 0 1 3 4c0-.6.4-1 1-1h3.5c.6 0 1 .4 1 1 0 1.3.2 2.5.6 3.6.1.3 0 .7-.2 1z"/></svg>9471 2658</span>
    </footer>
  </section>

  <!-- Roller Blinds & Sheers -->
  <section class="ad ad--sheers">
    <div class="photo" style="left:0;top:0;width:213px;height:341px;background:linear-gradient(90deg,#8d8d8d 0%,#f2f2f2 20%,#ffffff 50%,#e8e8e8 80%,#7c7c7c 100%)" role="img" aria-label="Girl opening sheer string curtains at a bright window"></div>
    <div class="brand" style="left:213px;top:0;width:151px;height:81px">
      <span class="brand-mark"></span>
      <span class="brand-name">Portals Drapes<br>&amp; Louvres</span>
    </div>
    <div class="panel panel--blue" style="left:213px;top:81px;width:151px;height:196px"></div>
    <div class="panel panel--white" style="left:213px;top:277px;width:151px;height:64px"></div>
    <div class="sale-banner" style="left:12px;top:4px;width:218px;--fs:35px">
      <span class="offer-tag">UP TO 40% OFF</span>
      <div class="sale-band"><span class="sale-title">SALE NOW ON</span></div>
      <span class="buy-tag">BUY NOW</span>
    </div>
    <ul class="feature-list" style="left:220px;top:104px;gap:8px;--ff:21px">
      <li class="feature"><svg class="feature-icon" viewBox="0 0 18 18" fill="none" stroke="#fff" stroke-width="1.6"><path d="M9 2 16 6 9 10 2 6z"/><path d="M2 9.5l7 4 7-4M2 13l7 4 7-4"/></svg><span class="feature-text">Huge Range<br>of Fabrics</span></li>
      <li class="feature"><svg class="feature-icon" viewBox="0 0 18 18" fill="none" stroke="#fff" stroke-width="1.6"><path d="M3 16C5 9 9 4 16 2c-1 6-5 10-11 11"/></svg><span class="feature-text">Modern Soft<br>Finish</span></li>
      <li class="feature"><svg class="feature-icon" viewBox="0 0 18 18" fill="none" stroke="#fff" stroke-width="1.6"><circle cx="9" cy="8" r="5.5"/><path d="M9 5.5l.8 1.7 1.8.2-1.3 1.2.3 1.8L9 9.5l-1.6.9.3-1.8-1.3-1.2 1.8-.2zM6 13l-1 4 4-2 4 2-1-4"/></svg><span class="feature-text">Perfect for<br>Any Room</span></li>
    </ul>
    <div class="badge" style="left:141px;top:231px">
      <span class="badge-ribbon badge-ribbon--left"></span><span class="badge-ribbon badge-ribbon--right"></span>
      <div class="badge-seal"><div class="badge-core"><span class="badge-small">Celebrating</span><span class="badge-big">13 YEARS</span><span class="badge-tiny">in Business</span></div></div>
    </div>
    <span class="cta" style="left:228px;top:298px;font-size:15px">Book a FREE<br>quote TODAY!</span>
    <footer class="contact-bar">
      <span class="contact-address">482 Upper Wattleby Road, Kestrel Heights</span>
      <span class="contact-phone"><svg viewBox="0 0 24 24" fill="#fff"><path d="M6.6 10.8a15 15 0 0 0 6.6 6.6l2.2-2.2c.3-.3.7-.4 1-.2 1.1.4 2.3.6 3.6.6.6 0 1 .4 1 1V20c0 .6-.4 1-1 1A17 17 0 0 1 3 4c0-.6.4-1 1-1h3.5c.6 0 1 .4 1 1 0 1.3.2 2.5.6 3.6.1.3 0 .7-.2 1z"/></svg>9471 2658</span>
    </footer>
  </section>

  <!-- Zipscreen Blinds -->
  <section class="ad ad--zip">
    <div class="photo" style="left:166px;top:29px;width:198px;height:312px;background:linear-gradient(180deg,#f4f5f6 0%,#e5e7ea 30%,#9b5a48 50%,#2c2c2c 68%,#8c8a84 100%)" role="img" aria-label="Brick alfresco area with dark zipscreen blinds and a hand holding a remote"></div>
    <div class="brand" style="left:222px;top:36px;width:118px;height:56px;background:transparent">
      <span class="brand-mark"></span>
      <span class="brand-name">Portals Drapes<br>&amp; Louvres</span>
    </div>
    <div class="panel panel--white" style="left:0;top:300px;width:190px;height:41px;clip-path:polygon(0 0,100% 0,88% 100%,0 100%)"></div>
    <div class="sale-banner" style="left:0;top:12px;width:228px;--fs:41px">
      <span class="offer-tag">UP TO 40% OFF</span>
      <div class="sale-band"><span class="sale-title">SALE NOW ON</span></div>
      <span class="buy-tag">BUY NOW</span>
    </div>
    <ul class="feature-list" style="left:14px;top:115px;gap:9px;--ff:21px">
      <li class="feature"><svg class="feature-icon" viewBox="0 0 18 18" fill="none" stroke="#fff" stroke-width="1.6"><circle cx="9" cy="8" r="6"/><circle cx="9" cy="8" r="2"/><path d="M11 14l5 2"/></svg><span class="feature-text">Made<br>to Measure</span></li>
      <li class="feature"><svg class="feature-icon" viewBox="0 0 18 18" fill="none" stroke="#fff" stroke-width="1.6"><path d="M3 3l12 12M15 3 3 15"/><circle cx="3.5" cy="3.5" r="1.5"/></svg><span class="feature-text">Fully<br>Installed</span></li>
      <li class="feature"><svg class="feature-icon" viewBox="0 0 18 18" fill="none" stroke="#fff" stroke-width="1.6"><path d="M9 1.5 15 4v5c0 4-3 6.5-6 7.5C6 15.5 3 13 3 9V4z"/><path d="M6.5 9l2 2 3-3.5"/></svg><span class="feature-text">Wind, Sun<br>&amp; Insect<br>Protection</span></li>
    </ul>
    <div class="badge" style="left:255px;top:220px">
      <span class="badge-ribbon badge-ribbon--left"></span><span class="badge-ribbon badge-ribbon--right"></span>
      <div class="badge-seal"><div class="badge-core"><span class="badge-small">Celebrating</span><span class="badge-big">13 YEARS</span><span class="badge-tiny">in Business</span></div></div>
    </div>
    <span class="cta" style="left:11px;top:303px;font-size:15px">Book a FREE<br>quote TODAY!</span>
    <footer class="contact-bar">
      <span class="contact-address">482 Upper Wattleby Road, Kestrel Heights</span>
      <span class="contact-phone"><svg viewBox="0 0 24 24" fill="#fff"><path d="M6.6 10.8a15 15 0 0 0 6.6 6.6l2.2-2.2c.3-.3.7-.4 1-.2 1.1.4 2.3.6 3.6.6.6 0 1 .4 1 1V20c0 .6-.4 1-1 1A17 17 0 0 1 3 4c0-.6.4-1 1-1h3.5c.6 0 1 .4 1 1 0 1.3.2 2.5.6 3.6.1.3 0 .7-.2 1z"/></svg>9471 2658</span>
    </footer>
  </section>

</main>
</body>
</html>
```